Coastline Premier Retreats Business Card Design

Design a business card for Coastline Premier Retreats. Look at the website for colors and reference. Card should have logo, name, title, office number, mobile number, email, URL and a tagline like, "Luxury Hotel & Resort Email Marketing" (This might change).

https://www.coastlinepremierretreats.example

The rest I will leave up to your imagination.

Contact Information for Business Card

Logo, name, title, office number, mobile number, email, URL and a tagline like, "Luxury Hotel & Resort Email Marketing" (This might change).

```html
<!DOCTYPE html>
<html lang="en">
<head>
<meta charset="utf-8">
<title>Coastline Premier Retreats – Business Card</title>
<link href="https://fonts.googleapis.com/css2?family=Jost:wght@400;500;700&display=swap" rel="stylesheet">
<style>
  :root {
    --bg: #d9d9d9;
    --card-white: #f7f7f7;
    --orange: #e46c1f;
    --orange-dark: #a84c10;
    --black: #060606;
    --ink: #111111;
    --white: #ffffff;
  }
  * { box-sizing: border-box; margin: 0; padding: 0; }
  html, body {
    width: 1200px; height: 900px; overflow: hidden;
    background: var(--bg);
    font-family: "Jost", "Futura", sans-serif;
  }
  .stage {
    width: 1200px; height: 900px;
    display: flex; flex-direction: column; align-items: center; justify-content: center;
    gap: 54px;
  }
  .card {
    width: 600px; height: 343px; position: relative; overflow: hidden;
    box-shadow: 0 10px 24px rgba(0,0,0,.25);
  }
  .card--front {
    background: var(--card-white);
    border-radius: 40px 0 40px 0;
    display: flex; align-items: center; justify-content: center;
  }
  .wordmark {
    font-family: "Jost", sans-serif; font-weight: 700;
    text-transform: uppercase; letter-spacing: 1px; line-height: 1.05;
  }
  .card--front .wordmark { color: var(--ink); font-size: 36px; text-align: center; }
  .card--back {
    background: var(--black);
    border-radius: 0 60px 0 60px;
  }
  .info-panel {
    position: absolute; left: 0; top: 0; bottom: 0; width: 350px;
    background: var(--orange);
    padding: 52px 36px 0 32px;
    color: var(--ink);
  }
  .info-panel::after {
    content: ""; position: absolute; top: 0; bottom: 0; right: 0; width: 12px;
    background: var(--orange-dark);
  }
  .notch {
    position: absolute; left: 350px; top: 122px; width: 12px; height: 14px;
    background: var(--black);
  }
  .person-name { font-weight: 700; font-size: 20px; letter-spacing: .5px; text-transform: uppercase; }
  .person-title { font-size: 17px; margin-top: 2px; }
  .contact-list { list-style: none; margin-top: 8px; font-size: 14px; }
  .contact-list li { display: flex; align-items: center; gap: 8px; line-height: 1.5; white-space: nowrap; }
  .contact-list li.spaced { margin-top: 14px; }
  .contact-list svg { width: 13px; height: 13px; flex: none; }
  .tagline { margin-top: 20px; font-size: 17px; line-height: 1.2; }
  .card--back .wordmark {
    position: absolute; right: 30px; bottom: 50px;
    color: var(--white); font-size: 22px; text-align: right;
  }
</style>
</head>
<body>
<main class="stage">
  <section class="card card--front" aria-label="Card front">
    <div class="wordmark">Coastline Premier<br>Retreats</div>
  </section>

  <section class="card card--back" aria-label="Card back">
    <div class="info-panel">
      <p class="person-name">Daniel Reyes</p>
      <p class="person-title">Director</p>
      <ul class="contact-list">
        <li>
          <svg viewBox="0 0 14 14" aria-hidden="true"><rect x="3.5" y="1" width="7" height="12" rx="1.2" fill="none" stroke="#111" stroke-width="1.2"/></svg>
          555.014.7300
        </li>
        <li class="spaced">
          <svg viewBox="0 0 14 14" aria-hidden="true"><path d="M3 1.5l2.3 2.6-1.3 1.5a7 7 0 0 0 4.4 4.4l1.5-1.3 2.6 2.3-1.5 1.6C6.5 12.6 1.4 7.5 1.4 3z" fill="#111"/></svg>
          555.014.2200
        </li>
        <li>
          <svg viewBox="0 0 14 14" aria-hidden="true"><rect x="1" y="3" width="12" height="8.5" fill="#111"/><path d="M1 3l6 4.5L13 3" fill="none" stroke="#e46c1f" stroke-width="1"/></svg>
          info@coastlinepremierretreats.example
        </li>
        <li>
          <svg viewBox="0 0 14 14" aria-hidden="true"><g fill="none" stroke="#111" stroke-width="1"><circle cx="7" cy="7" r="5.8"/><ellipse cx="7" cy="7" rx="2.6" ry="5.8"/><path d="M1.2 7h11.6M2 4h10M2 10h10"/></g></svg>
          www.coastlinepremierretreats.example
        </li>
        <li>
          <svg viewBox="0 0 14 14" aria-hidden="true"><path d="M7 13s-4.3-4.8-4.3-7.8a4.3 4.3 0 0 1 8.6 0C11.3 8.2 7 13 7 13z" fill="#111"/><circle cx="7" cy="5.2" r="1.6" fill="#e46c1f"/></svg>
          North America
        </li>
      </ul>
      <p class="tagline">Luxury Hotel &amp;<br>Resort Email Marketing</p>
    </div>
    <div class="notch"></div>
    <div class="wordmark">Coastline<br>Premier Retreats</div>
  </section>
</main>
</body>
</html>
```